Valdane Companies Business Card Design

We need a new business card for our Private Equity Real Estate Development firm, “Valdane” and our EB-5 regional center “Thornmere Regional Center” on one card. We prefer a design that is simple, elegant, and represents the luxury products we design and build as well as the financial security and stability our successful history has produced. We are an industry leader in our field and 3rd generation family business that has evolved into an institutional quality investment platform. Considered design size is standard business card dimensions (3.5 x 2 inches with an additional 1/8 inch space for design elements or backgrounds that extend beyond the finished size of your piece.

Target Market(s)

• High net worth individuals
• Highly skilled technical workers and physicians in the US seeking investment-based immigration opportunities
• Sophisticated private equity investors
• Intermediary partners include domestic attorneys and investment brokers, as well as international agent networks
• US real estate developers

Industry/Entity Type

Finance

Contact Information for Business Card

(Providing placeholder info for personal information, please design for longer character spaces, longer names and addresses etc..)
• Logo for Valdane
• Logo for Thornmere Regional Center
• Full name: Marcus Valdane
• Job title: CEO
• Email address: mvaldane@valdanecompanies.com
• Cell phone number: +1.555.314.2287
• Office number +1.555.628.4410
• Office address: Larkfield Court 5, 4817 Vista Orilla, Alder Bay, OR.
• Website: www.valdanecompanies.com

Font styles to use
Serif
Sans Serif

Colors
ec1f27
ffffff
000000

Requirements
Must have
• • Logo for Valdane
• • Logo for Thornmere Regional Center
• - Use rounded corners
• (See .ai file included for logos)
Nice to have
• • Simple, elegant design
• • Aesthetically compatible with our website design (www.valdanecompanies.com)
• • Color palette including but not limited to white, black, and red (as per logos)
Should not have
• - Not too much red color
• - Do not stack both logos on top of each other

```html
<!DOCTYPE html>
<html lang="en">
<head>
<meta charset="utf-8">
<title>Valdane Companies Business Card</title>
<link rel="stylesheet" href="https://fonts.googleapis.com/css2?family=Cinzel:wght@600&family=Libre+Baskerville:wght@400;700&family=Roboto:wght@400;500&display=swap">
<style>
  :root {
    --stage: #2a2a2a;
    --paper: #f3f3f3;
    --wine: #8e1438;
    --wine-deep: #6a0a26;
    --wine-bright: #c21d5a;
    --ink: #111111;
    --text-grey: #4a4a4a;
    --edge-grey: #b8b8b8;
    --rule: #c9c9c9;
    --white: #ffffff;
  }
  * { margin: 0; padding: 0; box-sizing: border-box; }
  html, body { width: 1200px; height: 960px; overflow: hidden; }
  body { background: var(--stage); position: relative; font-family: "Roboto", Arial, sans-serif; }

  .card { position: absolute; width: 598px; height: 342px; border-radius: 18px; overflow: hidden; }

  /* Front */
  .card-front { left: 315px; top: 113px; background: var(--paper); }
  .front-edge { position: absolute; left: 0; bottom: 0; width: 330px; height: 14px; background: var(--edge-grey); }
  .front-band {
    position: absolute; right: 0; bottom: 0; width: 283px; height: 34px;
    background: linear-gradient(90deg, var(--wine-deep), var(--wine) 60%, var(--wine-deep));
    clip-path: polygon(22px 0, 100% 0, 100% 100%, 0 100%);
    color: var(--white); font-size: 14px; letter-spacing: 0.2px;
    display: flex; align-items: center; justify-content: flex-end; padding-right: 36px;
  }

  .center-mark { position: absolute; left: 40px; top: 99px; width: 258px; text-align: center; color: var(--wine); font-family: "Cinzel", "Times New Roman", serif; font-weight: 600; }
  .center-mark .mark-square { display: block; width: 46px; height: 46px; margin: 0 auto 46px; background: var(--wine); }
  .center-mark .mark-name { display: block; font-size: 36px; line-height: 1; }
  .center-mark .mark-sub { display: block; font-size: 12px; letter-spacing: 6.4px; margin-top: 9px; margin-right: -6.4px; }

  .divider { position: absolute; left: 307px; top: 84px; width: 1px; height: 178px; background: var(--rule); }

  .contact { position: absolute; left: 331px; top: 85px; }
  .contact-name { font-family: "Libre Baskerville", Georgia, serif; font-weight: 700; font-size: 21px; color: var(--wine); line-height: 1.1; }
  .contact-title { font-family: "Libre Baskerville", Georgia, serif; font-size: 14px; color: var(--ink); margin-top: 0; }
  .contact-address { margin-top: 8px; font-size: 14px; line-height: 18px; color: var(--text-grey); }
  .contact-lines { margin-top: 9px; font-size: 14px; line-height: 19px; color: var(--text-grey); }
  .contact-lines .label { color: var(--wine); font-weight: 500; }

  /* Back */
  .card-back {
    left: 312px; top: 472px;
    background: radial-gradient(ellipse 360px 300px at 340px 140px, var(--wine-bright), var(--wine) 55%, var(--wine-deep));
  }
  .back-mark { position: absolute; right: 28px; top: 236px; text-align: center; color: var(--white); font-family: "Cinzel", "Times New Roman", serif; font-weight: 600; }
  .back-mark .mark-name { display: block; font-size: 44px; line-height: 1; }
  .back-mark .mark-sub { display: block; font-size: 13px; letter-spacing: 8px; margin-top: 2px; margin-right: -8px; }
  .back-url { position: absolute; right: 30px; top: 302px; color: var(--white); font-size: 15px; letter-spacing: 0.3px; }
</style>
</head>
<body>
  <section class="card card-front" aria-label="Business card front">
    <div class="center-mark">
      <span class="mark-square" aria-hidden="true"></span>
      <span class="mark-name">Thornmere</span>
      <span class="mark-sub">REGIONAL CENTER</span>
    </div>
    <div class="divider"></div>
    <div class="contact">
      <p class="contact-name">MARCUS VALDANE</p>
      <p class="contact-title">CEO</p>
      <p class="contact-address">Larkfield Court 5<br>4817 Vista Orilla<br>Alder Bay, OR.</p>
      <p class="contact-lines">
        <span class="label">Phone:</span> +1.555.628.4410<br>
        <span class="label">Email:</span> +1.555.314.2287<br>
        mvaldane@valdanecompanies.com
      </p>
    </div>
    <div class="front-edge"></div>
    <div class="front-band">www.valdanecompanies.com</div>
  </section>

  <section class="card card-back" aria-label="Business card back">
    <div class="back-mark">
      <span class="mark-name">VALDANE</span>
      <span class="mark-sub">CAPITAL</span>
    </div>
    <p class="back-url">www.valdanecompanies.com</p>
  </section>
</body>
</html>
```